Company or website name
- Velmira, LLC
- Velmira, LLC
- Describe your company and organization and target audience
- Velmira, LLC is a research, science and technology based manufacturing company that formulates, develops, manufactures and packages a full complement of personal care products for domestic and international concerns. We private label and contract package personal care products, cosmetics, bath salts and powders and home fragrance products. Velmira is conveniently located in Southern California adjacent to major transportation hubs and international airports. We utilize earth friendly, green manufacturing processes, maximize the use of renewable resource raw materials and minimize the use of non-renewable and petrochemical based raw materials. We provide formulation and product development services with low minimum order quantities and short lead times. Velmira is the intersection between nature, science, beauty and innovation. We are a B-2-B company.
- The design should have the following
- We're looking for an ad design that can be used for both banner and column use online and in print. We manufacture bath and body products such as bath salts, body washes, body powders, bath oils and bubble baths, hair care products such as shampoos, conditioners and styling aids, skin care products such as anti-aging creams, cleansers, masks, toners and serums, color cosmetics such as eyeliners, mascaras, foundations and mineral make-up powders, manicure/pedicure products such as cuticle oils, sugar and salt scrubs and foot soaks/softeners and spa products such as seaweed wraps, cellulite creams, body masks, massage oils and candles. Our strengths are natural and organic product formulation, low minimums, competitive prices, complete research &development services new and innovative ingredients and fast turnaround times. Examples can be found at the following sites: http://www.glintor.com/ http://www.grovewellboard.org/ http://www.tessaloomjournal.com/ http://nerwast.org/images/downloads/bulletins/2009-10-bulletin.pdf http://www.pantrykestrelworks.com/

```html
<!DOCTYPE html>
<html lang="en">
<head>
<meta charset="utf-8">
<title>Velmira – Bath Products Ad Set</title>
<link href="https://fonts.googleapis.com/css2?family=EB+Garamond:wght@400;500&display=swap" rel="stylesheet">
<style>
  :root{
    --stage-light:#8a8a8a;
    --stage-dark:#4a4a4a;
    --navy:#1c2a86;
    --band:#15308c;
    --ink:#222;
    --rule:#9a9a9a;
    --paper:#ffffff;
    --logo-gold:#b8872a;
    --photo-a:#c9d6ea;
    --photo-b:#7e93bd;
    --photo-c:#6f8f4a;
  }
  *{box-sizing:border-box;margin:0;padding:0}
  html,body{width:1200px;height:1043px;overflow:hidden}
  body{
    position:relative;
    background:radial-gradient(ellipse at 60% 30%,var(--stage-light),var(--stage-dark));
    font-family:"EB Garamond",Georgia,serif;
    color:var(--ink);
  }
  .ad{position:absolute;background:var(--paper);display:flex;flex-direction:column;overflow:hidden}
  .ad-square{left:48px;top:169px;width:426px;height:427px}
  .ad-poster{left:491px;top:12px;width:426px;height:586px}
  .ad-column{left:936px;top:12px;width:214px;height:587px}
  .ad-banner{left:42px;top:604px;width:1108px;height:421px;flex-direction:row}

  .photo{
    position:relative;flex:none;width:100%;
    background:
      radial-gradient(circle at 55% 25%,rgba(130,190,80,.75),transparent 30%),
      radial-gradient(circle at 20% 60%,rgba(90,150,70,.45),transparent 35%),
      linear-gradient(135deg,var(--photo-a),var(--photo-b));
  }
  .ad-square .photo{height:208px}
  .ad-poster .photo{height:261px}
  .ad-column .photo{height:132px}
  .ad-banner .photo{width:646px;height:100%}

  .logo{
    position:absolute;left:8px;top:8px;display:flex;align-items:center;gap:5px;
    background:var(--paper);border-radius:20px;padding:4px 12px 4px 6px;
    color:var(--logo-gold);font-weight:500;
  }
  .logo-dot{border-radius:50%;background:var(--logo-gold);flex:none}
  .ad-square .logo{font-size:22px}
  .ad-square .logo-dot{width:12px;height:12px}
  .ad-poster .logo{font-size:24px}
  .ad-poster .logo-dot{width:13px;height:13px}
  .ad-column .logo{font-size:11px;left:3px;top:3px;padding:2px 6px 2px 3px}
  .ad-column .logo-dot{width:6px;height:6px}
  .ad-banner .logo{font-size:26px;top:14px;left:8px}
  .ad-banner .logo-dot{width:14px;height:14px}

  .copy{flex:1;display:flex;flex-direction:column;align-items:center;text-align:center}
  .ad-banner .copy{border-top:3px solid var(--band);margin-left:5px}
  .headline{color:var(--navy);font-weight:400;line-height:1.2}
  .features{text-transform:uppercase;line-height:1.6}
  .rule{border:0;border-top:1px solid var(--rule);width:86%}
  .badge{background:var(--band);color:#fff;font-weight:500;text-transform:uppercase;letter-spacing:.3px}
  .products{display:flex;justify-content:center;align-items:flex-end}
  .labels{text-transform:uppercase}
  .footer{background:var(--band);color:#fff;width:100%;text-align:center;line-height:1.4;margin-top:auto}

  .product{flex:none}
  .p-gel{background:linear-gradient(90deg,#e99a18,#ffd27a,#e38f10);border-radius:3px 3px 1px 1px}
  .p-salt{background:radial-gradient(ellipse at 50% 30%,#fafafa 40%,#5b3a22 42%);border-radius:50%/40%}
  .p-powder{background:linear-gradient(180deg,#c9d2e0,#6f7d98);border-radius:6px}
  .p-lotion{background:linear-gradient(90deg,#f3a36a,#ffe0c6,#ef8c44);border-radius:40% 40% 6px 6px}
  .p-oil{background:linear-gradient(90deg,#3f7a2c,#8dc26b);border-radius:4px}

  /* square */
  .ad-square .headline{font-size:21.5px;margin-top:6px}
  .ad-square .features{font-size:11px;margin-top:7px}
  .ad-square .rule{margin-top:4px}
  .ad-square .badge{font-size:9px;padding:0 4px;margin-top:6px}
  .ad-square .products{gap:20px;margin-top:6px;height:48px}
  .ad-square .labels{font-size:8px;margin-top:6px}
  .ad-square .footer{font-size:8.3px;padding:4px 0}

  /* poster */
  .ad-poster .headline{font-size:27px;margin-top:8px}
  .ad-poster .features{font-size:11.5px;margin-top:10px;line-height:1.65}
  .ad-poster .rule{margin-top:14px}
  .ad-poster .badge{font-size:14px;padding:1px 6px;margin-top:18px}
  .ad-poster .products{gap:26px;margin-top:10px;height:76px}
  .ad-poster .labels{font-size:11px;margin-top:8px}
  .ad-poster .footer{font-size:14px;padding:8px 0 6px}

  /* column */
  .ad-column .headline{font-size:14.5px;margin-top:8px}
  .ad-column .features{font-size:6.6px;margin-top:10px}
  .ad-column .rule{margin-top:6px}
  .ad-column .badge{font-size:9px;padding:0 4px;margin-top:10px}
  .ad-column .grid{display:grid;grid-template-columns:1fr 1fr;width:100%;margin-top:6px}
  .ad-column .cell{display:flex;flex-direction:column;align-items:center;justify-content:flex-end;height:72px;font-size:9px;text-transform:uppercase;gap:6px}
  .ad-column .divider{grid-column:1/3;border-top:1px solid var(--rule);width:86%;justify-self:center;margin:18px 0 14px}
  .ad-column .single{grid-column:1/3}
  .ad-column .footer{font-size:6.6px;padding:3px 0}

  /* banner */
  .ad-banner .headline{font-size:29.5px;margin-top:14px;line-height:1.3}
  .ad-banner .rule{margin-top:22px}
  .ad-banner .features{font-size:15px;margin-top:16px;line-height:1.6}
  .ad-banner .badge{font-size:15px;padding:2px 7px;margin-top:22px}
  .ad-banner .products{gap:28px;margin-top:14px;height:80px}
  .ad-banner .labels{font-size:13px;margin-top:8px}
  .ad-banner .footer{font-size:16px;padding:10px 0 8px}
</style>
</head>
<body>

<section class="ad ad-square">
  <div class="photo" role="img" aria-label="Gloved hand using a dropper over a seedling in a test tube">
    <div class="logo"><span class="logo-dot"></span>Velmira</div>
  </div>
  <div class="copy">
    <h2 class="headline">Creating Innovative Products<br>by Blending Science and Nature</h2>
    <p class="features">FDA Registered &nbsp;I&nbsp; Fast Turnaround &nbsp;I&nbsp; Low Minimums<br>Competitive Pricing &nbsp;I&nbsp; cGMP Quality Control</p>
    <hr class="rule">
    <span class="badge">Bath Products</span>
    <div class="products">
      <div class="product p-gel" role="img" aria-label="Bath gel tube" style="width:14px;height:42px"></div>
      <div class="product p-salt" role="img" aria-label="Bowl of bath salts" style="width:36px;height:22px"></div>
      <div class="product p-powder" role="img" aria-label="Body powder jar" style="width:36px;height:26px"></div>
      <div class="product p-lotion" role="img" aria-label="Lotion bottle" style="width:16px;height:44px"></div>
      <div class="product p-oil" role="img" aria-label="Bath oil box and bottle" style="width:26px;height:44px"></div>
    </div>
    <p class="labels">Bath Gels &nbsp;I&nbsp; Bath Salts &nbsp;I&nbsp; Body Powders &nbsp;I&nbsp; Lotions &nbsp;I&nbsp; Bath Oils</p>
    <p class="footer">4820 W. Calloway Avenue Building 210, Brisa Vale, CA 92814, &nbsp;555.302.4187 P 555.302.4188 F info@velmira.com</p>
  </div>
</section>

<section class="ad ad-poster">
  <div class="photo" role="img" aria-label="Gloved hand using a dropper over a seedling in a test tube">
    <div class="logo"><span class="logo-dot"></span>Velmira</div>
  </div>
  <div class="copy">
    <h2 class="headline">Creating Innovative Products<br>by Blending Science and Nature</h2>
    <p class="features">FDA Registered &nbsp;I&nbsp; Fast Turnaround &nbsp;I&nbsp; Low Minimums<br>Competitive Pricing &nbsp;I&nbsp; cGMP Quality Control</p>
    <hr class="rule">
    <span class="badge">Bath Products</span>
    <div class="products">
      <div class="product p-gel" role="img" aria-label="Bath gel tube" style="width:22px;height:70px"></div>
      <div class="product p-salt" role="img" aria-label="Bowl of bath salts" style="width:60px;height:36px"></div>
      <div class="product p-powder" role="img" aria-label="Body powder jar" style="width:60px;height:40px"></div>
      <div class="product p-lotion" role="img" aria-label="Lotion bottle" style="width:28px;height:74px"></div>
      <div class="product p-oil" role="img" aria-label="Bath oil box and bottle" style="width:46px;height:72px"></div>
    </div>
    <p class="labels">Bath Gels &nbsp;I&nbsp; Bath Salts &nbsp;I&nbsp; Body Powders &nbsp;I&nbsp; Lotions &nbsp;I&nbsp; Bath Oils</p>
    <p class="footer">4820 W. Calloway Avenue Building 210, Brisa Vale, CA 92814<br>555.302.4187 P 555.302.4188 F info@velmira.com</p>
  </div>
</section>

<section class="ad ad-column">
  <div class="photo" role="img" aria-label="Gloved hand using a dropper over a seedling in a test tube">
    <div class="logo"><span class="logo-dot"></span>Velmira</div>
  </div>
  <div class="copy">
    <h2 class="headline">Creating Innovative Products<br>by Blending Science and Nature</h2>
    <p class="features">FDA Registered &nbsp;I&nbsp; Fast Turnaround &nbsp;I&nbsp; Low Minimums<br>Competitive Pricing &nbsp;I&nbsp; cGMP Quality Control</p>
    <hr class="rule">
    <span class="badge">Bath Products</span>
    <div class="grid">
      <div class="cell"><div class="product p-gel" role="img" aria-label="Bath gel tube" style="width:16px;height:46px"></div>Bath Gels</div>
      <div class="cell"><div class="product p-salt" role="img" aria-label="Bowl of bath salts" style="width:46px;height:28px"></div>Bath Salts</div>
      <div class="divider"></div>
      <div class="cell"><div class="product p-powder" role="img" aria-label="Body powder jar" style="width:46px;height:30px"></div>Body Powders</div>
      <div class="cell"><div class="product p-lotion" role="img" aria-label="Lotion bottle" style="width:20px;height:50px"></div>Lotions</div>
      <div class="divider"></div>
      <div class="cell single"><div class="product p-oil" role="img" aria-label="Bath oil box and bottle" style="width:38px;height:52px"></div>Bath Oils</div>
    </div>
    <p class="footer">4820 W. Calloway Avenue Building 210, Brisa Vale, CA 92814<br>555.302.4187 P 555.302.4188 F info@velmira.com</p>
  </div>
</section>

<section class="ad ad-banner">
  <div class="photo" role="img" aria-label="Gloved hand using a dropper over a seedling in a test tube">
    <div class="logo"><span class="logo-dot"></span>Velmira</div>
  </div>
  <div class="copy">
    <h2 class="headline">Creating Innovative Products<br>by Blending Science and Nature</h2>
    <hr class="rule">
    <p class="features">FDA Registered &nbsp;I&nbsp; Fast Turnaround &nbsp;I&nbsp; Low Minimums<br>Competitive Pricing &nbsp;I&nbsp; cGMP Quality Control</p>
    <hr class="rule" style="margin-top:12px">
    <span class="badge">Bath Products</span>
    <div class="products">
      <div class="product p-gel" role="img" aria-label="Bath gel tube" style="width:24px;height:74px"></div>
      <div class="product p-salt" role="img" aria-label="Bowl of bath salts" style="width:62px;height:38px"></div>
      <div class="product p-powder" role="img" aria-label="Body powder jar" style="width:62px;height:42px"></div>
      <div class="product p-lotion" role="img" aria-label="Lotion bottle" style="width:30px;height:78px"></div>
      <div class="product p-oil" role="img" aria-label="Bath oil box and bottle" style="width:48px;height:76px"></div>
    </div>
    <p class="labels">Bath Gels &nbsp;I&nbsp; Bath Salts &nbsp;I&nbsp; Body Powders &nbsp;I&nbsp; Lotions &nbsp;I&nbsp; Bath Oils</p>
    <p class="footer">4820 W. Calloway Avenue Building 210, Brisa Vale, CA 92814<br>555.302.4187 P 555.302.4188 F info@velmira.com</p>
  </div>
</section>

</body>
</html>
```